Corvell Keystone Lighting Commercial & Residential Landscape Lighting

Hello, I am looking for an Ad Design that I can use to promote ads on Plumora and other social media platforms. I want this ad to be a split screen ad meaning one photo at the top and one photo at the bottom to include a southern style home without outdoor landscape lighting & then the same picture at the bottom with outdoor landscape lighting. Add text to the graphic that talks about the difference landscape lighting does to your home. I want this ad to look professional and have professional design elements to the ad. I also have a logo I have uploaded below. We specialize in commercial grade outdoor landscape lighting, custom flag poles, outdoor audio, and we are locally and veteran owned. We offer lifetime warranty and quarterly maintenance on products.

```html
<!DOCTYPE html>
<html lang="en">
<head>
<meta charset="utf-8">
<title>Corvell Keystone Lighting – Social Ad</title>
<link rel="stylesheet" href="https://fonts.googleapis.com/css2?family=Poppins:wght@400;500;800&family=Oswald:wght@400&display=swap">
<style>
  :root {
    --canvas: #ffffff;
    --ink: #000000;
    --cream: #fbe0c0;
    --gold: #e6a82e;
    --amber: #f0a33a;
    --dusk: #1f3d8a;
    --lawn: #3a5a1e;
  }
  * { margin: 0; padding: 0; box-sizing: border-box; }
  html, body { width: 1200px; height: 586px; overflow: hidden; background: var(--canvas); }
  .ad {
    position: absolute; left: 320px; top: 13px;
    width: 560px; height: 560px;
    font-family: "Poppins", sans-serif;
  }
  .ad__shapes { position: absolute; inset: 0; width: 560px; height: 560px; }
  .brand {
    position: absolute; left: 26px; top: 70px;
    color: var(--amber); font-weight: 400; line-height: 1;
  }
  .brand__name { font-size: 46px; letter-spacing: 2px; }
  .brand__tag { font-size: 11.5px; letter-spacing: 3.6px; margin-top: 10px; }
  .headline { position: absolute; left: 26px; top: 244px; line-height: 1; }
  .headline__lead { color: var(--cream); font-size: 27px; font-weight: 500; line-height: 32px; display: block; }
  .headline__key { color: var(--gold); display: block; }
  .headline__your { font-size: 53px; font-weight: 500; line-height: 48px; margin-top: 8px; }
  .headline__home { font-size: 52px; font-weight: 800; line-height: 50px; }
  .headline__feels { font-size: 53px; font-weight: 500; line-height: 48px; }
  .contact {
    position: absolute; left: 26px; top: 500px;
    font-family: "Oswald", sans-serif; color: var(--cream);
    font-size: 18px; line-height: 22px; list-style: none;
  }
  .contact__item { display: flex; align-items: center; gap: 8px; }
  .contact__item svg { width: 16px; height: 16px; fill: var(--amber); }
</style>
</head>
<body>
<main class="ad">
  <svg class="ad__shapes" viewBox="0 0 1050 1050" aria-hidden="false">
    <defs>
      <linearGradient id="pathGlow" x1="0" y1="0" x2="0" y2="1">
        <stop offset="0" stop-color="#000"/>
        <stop offset="0.55" stop-color="#1a140c"/>
        <stop offset="1" stop-color="#4a3517"/>
      </linearGradient>
      <radialGradient id="houseDay" cx="0.5" cy="0.35" r="0.7">
        <stop offset="0" stop-color="#2c55b0"/>
        <stop offset="0.55" stop-color="#5a3a22"/>
        <stop offset="1" stop-color="var(--lawn)"/>
      </radialGradient>
      <radialGradient id="houseLit" cx="0.5" cy="0.45" r="0.7">
        <stop offset="0" stop-color="#e0a040"/>
        <stop offset="0.45" stop-color="#4a3218"/>
        <stop offset="1" stop-color="#2f5a1a"/>
      </radialGradient>
    </defs>
    <rect class="backdrop" width="1050" height="1050" fill="var(--ink)"/>
    <rect class="backdrop__path" role="img" aria-label="Night pathway lined with low garden lights" x="0" y="700" width="590" height="350" fill="url(#pathGlow)"/>
    <path class="corner-cut" d="M859 0 H1050 V250 A200 200 0 0 0 859 15 Z" fill="var(--canvas)"/>
    <rect class="band band--cream" x="584" y="0" width="275" height="520" fill="var(--cream)"/>
    <rect class="band band--gold" x="584" y="520" width="275" height="530" fill="var(--gold)"/>
    <circle class="ring ring--top" cx="724" cy="297" r="280" fill="var(--cream)"/>
    <circle class="photo photo--unlit" role="img" aria-label="Southern style home at dusk without landscape lighting" cx="724" cy="297" r="258" fill="url(#houseDay)"/>
    <circle class="ring ring--bottom" cx="724" cy="728" r="274" fill="var(--gold)"/>
    <circle class="photo photo--lit" role="img" aria-label="Same home at night with warm landscape lighting" cx="724" cy="728" r="255" fill="url(#houseLit)"/>
  </svg>

  <div class="brand">
    <div class="brand__name">CORVELL</div>
    <div class="brand__tag">KEYSTONE LIGHTING</div>
  </div>

  <h1 class="headline">
    <span class="headline__lead">Lighting That</span>
    <span class="headline__lead">Changes How</span>
    <span class="headline__key headline__your">Your</span>
    <span class="headline__key headline__home">Home</span>
    <span class="headline__key headline__feels">Feels</span>
  </h1>

  <ul class="contact">
    <li class="contact__item">
      <svg viewBox="0 0 24 24"><path d="M2 5h20v14H2z M2 5l10 8 10-8" stroke="#000" stroke-width="1.5"/></svg>
      (555)203-4718
    </li>
    <li class="contact__item">
      <svg viewBox="0 0 24 24"><path d="M6.6 10.8a15 15 0 0 0 6.6 6.6l2.2-2.2a1 1 0 0 1 1-.25 11.4 11.4 0 0 0 3.6.57 1 1 0 0 1 1 1V20a1 1 0 0 1-1 1A17 17 0 0 1 3 4a1 1 0 0 1 1-1h3.5a1 1 0 0 1 1 1 11.4 11.4 0 0 0 .57 3.6 1 1 0 0 1-.25 1z"/></svg>
      hello@corvellkeystone.com
    </li>
  </ul>
</main>
</body>
</html>
```